RW Framewell Inc Business cards

We need business cards using our existing logo but slightly modified. Right now the logo says RW Loadbearing Masonry. We want to keep the RW part of the design, but replace the Structural Concrete portion with "FRAMEWELL". Please see the attached file.
Ideally this would be a blank template so we can add Different Names, titles, and phone numbers later.
On the one side we want only the logo and on the other side the detail. I'm attaching an example for you to see.
Please reach out with any other questions. Our address and other details will be given out once we find a design we like.

Target Market(s)

Construction Industry

```html
<!DOCTYPE html>
<html lang="en">
<head>
<meta charset="utf-8">
<title>RW Framewell Inc Business Cards</title>
<link href="https://fonts.googleapis.com/css2?family=Roboto:wght@400;500;700&display=swap" rel="stylesheet">
<style>
  :root {
    --backdrop: #3b3b3c;
    --card: #1f1f21;
    --card-edge: #2a2a2c;
    --brand-blue: #2f64b3;
    --ink-light: #ffffff;
    --ink-muted: #8d8d90;
    --ink-soft: #d9d9db;
  }
  * { margin: 0; padding: 0; box-sizing: border-box; }
  html, body { width: 799px; height: 1200px; overflow: hidden; }
  body {
    background: var(--backdrop);
    font-family: "Roboto", Arial, sans-serif;
    position: relative;
  }
  .card {
    position: absolute;
    left: 80px;
    width: 640px;
    height: 366px;
    background: var(--card);
    border: 1px solid var(--card-edge);
    border-radius: 4px;
    box-shadow: 0 18px 40px rgba(0,0,0,0.45);
  }
  .card--front { top: 150px; }
  .card--back { top: 690px; }

  .wordmark {
    font-family: "Roboto", Arial, sans-serif;
    font-weight: 700;
    letter-spacing: 6px;
    white-space: nowrap;
  }
  .card--front .wordmark {
    position: absolute;
    left: 0; right: 0; top: 150px;
    text-align: center;
    font-size: 46px;
    color: var(--ink-muted);
  }
  .card--back .wordmark {
    position: absolute;
    left: 240px; top: 70px;
    font-size: 40px;
    color: var(--ink-light);
  }

  .identity {
    position: absolute;
    right: 340px; top: 196px;
    text-align: right;
    color: var(--ink-light);
  }
  .identity__name {
    font-size: 22px;
    font-weight: 500;
    color: var(--brand-blue);
  }
  .identity__title {
    font-size: 16px;
    margin-top: 2px;
    padding-bottom: 8px;
    border-bottom: 1.5px solid var(--brand-blue);
  }
  .identity__address {
    font-size: 16px;
    line-height: 22px;
    margin-top: 8px;
    color: var(--ink-soft);
  }

  .contacts {
    position: absolute;
    left: 340px; top: 236px;
    list-style: none;
    color: var(--ink-light);
    font-size: 17px;
  }
  .contacts__item {
    display: flex;
    align-items: center;
    gap: 14px;
    height: 28px;
  }
  .contacts__icon { width: 16px; height: 16px; fill: var(--brand-blue); flex: none; }
</style>
</head>
<body>
  <section class="card card--front" aria-label="Card front">
    <div class="wordmark">RW FRAMEWELL</div>
  </section>

  <section class="card card--back" aria-label="Card back">
    <div class="wordmark">RW FRAMEWELL</div>

    <div class="identity">
      <div class="identity__name">Daniel RW Reyes</div>
      <div class="identity__title">Managing Director</div>
      <div class="identity__address">418 Linden Ave., Oak Falls,<br>Oregon, US 974011</div>
    </div>

    <ul class="contacts">
      <li class="contacts__item">
        <svg class="contacts__icon" viewBox="0 0 16 16" aria-hidden="true"><path d="M2 3h12v3l-3 1-1-2H6L5 7 2 6z M3 8h10l1 6H2z"/></svg>
        <span>555-014-2270</span>
      </li>
      <li class="contacts__item">
        <svg class="contacts__icon" viewBox="0 0 16 16" aria-hidden="true"><path d="M1 3h14v10H1z M2 4l6 5 6-5" fill="var(--brand-blue)" stroke="var(--card)" stroke-width="1.2"/></svg>
        <span>daniel@framewellbuild.com</span>
      </li>
      <li class="contacts__item">
        <svg class="contacts__icon" viewBox="0 0 16 16" aria-hidden="true"><circle cx="8" cy="8" r="7"/><path d="M1 8h14 M8 1c-3 3-3 11 0 14 M8 1c3 3 3 11 0 14" fill="none" stroke="var(--card)" stroke-width="1"/></svg>
        <span>www.framewellbuild.com</span>
      </li>
    </ul>
  </section>
</body>
</html>
```